Kestrada LLC, needs a web page no more than 5 pages (for now)

Kestrada is a general contractor. Our services include general contracting, design-build construction, disaster recovery and environmental remediation. Our main clients are PMX, TQ, State and Local Gov't Agencies, Hospitals and Schools. Kestrada is also a SDVOSB.

```html
<!DOCTYPE html>
<html lang="en">
<head>
<meta charset="utf-8">
<title>Kestrada LLC — General Contracting</title>
<link href="https://fonts.googleapis.com/css2?family=Poppins:wght@300;400;500;600;700&display=swap" rel="stylesheet">
<style>
:root{
  --gold:#c49a3f;
  --gold-dark:#a9822f;
  --beige:#e4d2a6;
  --dark:#2b2b2b;
  --ink:#222;
  --muted:#666;
  --line:#d9d9d9;
  --white:#fff;
}
*{box-sizing:border-box;margin:0;padding:0}
html,body{width:1200px;height:5277px;overflow:hidden}
body{position:relative;font-family:"Poppins",sans-serif;color:var(--ink);background:var(--white)}
.abs{position:absolute}
.btn{position:absolute;display:flex;align-items:center;justify-content:center;background:var(--gold);color:var(--white);font-size:12px;font-weight:500;letter-spacing:.5px;text-transform:uppercase}
.btn--light{background:var(--white);color:var(--ink)}
.photo{position:absolute}
.section-title{position:absolute;left:0;width:1200px;text-align:center;font-size:38px;font-weight:400}
.section-title b{font-weight:700}

/* top bar */
.topbar{position:absolute;left:0;top:0;width:1200px;height:36px}
.topbar__gold{position:absolute;inset:0}
.topbar__social{position:absolute;left:430px;top:10px;display:flex;gap:22px}
.topbar__social span{width:14px;height:14px;border-radius:50%;background:rgba(255,255,255,.85)}
.topbar__contact{position:absolute;left:736px;top:9px;display:flex;gap:26px;color:var(--white);font-size:12px}
.topbar__contact div{display:flex;align-items:center;gap:8px}
.logo{position:absolute;display:flex;align-items:center;gap:10px;color:var(--gold);font-weight:600;letter-spacing:1px}
.logo i{display:block;border-radius:50%;background:var(--gold)}
.nav{position:absolute;top:72px;left:389px;display:flex;gap:0;font-size:13px;color:#333}
.nav a{text-decoration:none;color:inherit;margin-right:40px}

/* hero */
.hero-photo{left:0;top:123px;width:1200px;height:637px;background:linear-gradient(100deg,#6d6a63 0%,#9a8f80 35%,#c88d5c 60%,#7b6f64 100%)}
.hero__title{position:absolute;left:160px;top:326px;color:var(--white);font-size:46px;font-weight:600;line-height:54px}
.hero__sub{position:absolute;left:160px;top:440px;color:var(--white);font-size:13px;line-height:17px}

/* about */
.about{position:absolute;left:0;top:727px;width:1200px;height:560px;background:var(--dark)}
.about__text{position:absolute;left:265px;top:862px;width:670px;text-align:center;color:#eee;font-size:13.5px;line-height:19px}
.about__text p{margin-bottom:19px}

/* services */
.card{position:absolute;background:var(--white);box-shadow:0 6px 30px rgba(0,0,0,.12);padding:42px 42px}
.card h3{font-size:23px;font-weight:400;margin-bottom:20px}
.card p{font-size:13px;line-height:19.5px;color:var(--muted);margin-bottom:19px}
.card a{font-size:13px;color:var(--gold);text-decoration:none;border-bottom:1px solid var(--gold);padding-bottom:2px}

/* projects */
.projects{position:absolute;left:0;top:2888px;width:1200px;height:737px;background:var(--dark)}
.project{position:absolute;top:3088px;width:277px;text-align:center;color:var(--white)}
.project .photo{position:relative;width:277px;height:318px}
.project h4{font-size:15px;font-weight:500;margin-top:20px}
.project p{font-size:11.5px;line-height:14px;margin:8px 6px 0;color:#ddd}

/* why */
.why{position:absolute;top:3769px;width:220px;text-align:center}
.why__ring{width:144px;height:144px;margin:0 auto;border:2px dashed var(--gold);border-radius:50%;display:flex;align-items:center;justify-content:center}
.why h5{font-size:14.5px;font-weight:600;margin-top:20px;line-height:18px}

/* clients */
.client{position:absolute;top:4104px;width:190px;text-align:center}
.client__mark{width:118px;height:118px;margin:0 auto;border-radius:50%}
.client h6{font-size:14px;font-weight:600;margin-top:18px;line-height:17px}

/* contact */
.contact-photo{left:0;top:4325px;width:1200px;height:652px;background:linear-gradient(120deg,#dcdcdc 0%,#c8c7c3 45%,#e2c35a 75%,#bdbab4 100%)}
.contact-card{position:absolute;left:362px;top:4407px;width:476px;height:570px;background:var(--white)}
.contact-card__eyebrow{position:absolute;top:52px;width:100%;text-align:center;font-size:13px;color:#555}
.contact-card__title{position:absolute;top:74px;width:100%;text-align:center;font-size:30px;font-weight:500}
.field{position:absolute;border-bottom:1px solid var(--line);font-size:11.5px;color:#888;padding-bottom:14px}
.captcha{position:absolute;left:124px;top:4854px;width:232px;height:56px;border:1px solid #d3d3d3;border-radius:3px;background:#f9f9f9;font-size:11px;color:#444;display:flex;align-items:center;padding-left:12px;gap:10px}
.captcha i{width:20px;height:20px;border:2px solid #c1c1c1;border-radius:2px;background:var(--white)}
.captcha b{position:absolute;right:14px;top:12px;width:26px;height:26px;border-radius:50%;background:#9aa7c4}

/* footer */
.footer{position:absolute;left:0;top:4977px;width:1200px;height:300px;background:var(--dark);color:var(--white)}
.footer__col{position:absolute;top:58px;font-size:12px}
.footer__col h6{font-size:13px;font-weight:600;margin-bottom:16px}
.footer__col li{list-style:none;height:30px;color:#ddd}
.footer__row{display:flex;align-items:center;gap:12px}
.footer__social{display:flex;gap:30px;margin-top:22px}
.footer__social span{width:14px;height:14px;border-radius:50%;background:#eee}
.footer__copy{position:absolute;top:262px;width:100%;text-align:center;font-size:11px;color:#ccc}
</style>
</head>
<body>

<!-- header -->
<div class="topbar">
  <svg class="topbar__gold" width="1200" height="36"><polygon points="358,0 1200,0 1200,36 392,36" fill="var(--gold)"/></svg>
  <div class="topbar__social"><span></span><span></span><span></span></div>
  <div class="topbar__contact">
    <div><svg width="12" height="12" viewBox="0 0 24 24"><path fill="#fff" d="M6.6 10.8a15 15 0 0 0 6.6 6.6l2.2-2.2a1 1 0 0 1 1-.25 11.4 11.4 0 0 0 3.6.57 1 1 0 0 1 1 1V20a1 1 0 0 1-1 1A17 17 0 0 1 3 4a1 1 0 0 1 1-1h3.5a1 1 0 0 1 1 1c0 1.25.2 2.45.57 3.57a1 1 0 0 1-.25 1z"/></svg>+1 555 014 2270</div>
    <div><svg width="13" height="10" viewBox="0 0 26 20"><rect width="26" height="20" fill="#fff"/><path d="M0 0l13 10L26 0" stroke="var(--gold)" stroke-width="2" fill="none"/></svg>hello@kestrada-build.com</div>
  </div>
</div>
<div class="logo" style="left:160px;top:52px;font-size:22px"><i style="width:14px;height:14px"></i>KESTRADA</div>
<nav class="nav"><a>ABOUT</a><a>SERVICES</a><a style="margin-right:32px">OUR CLIENTS</a><a>PROJECTS</a><a>CONTACT US</a></nav>
<div class="btn" style="left:887px;top:61px;width:151px;height:38px">Get in touch</div>

<!-- hero -->
<div class="photo hero-photo" role="img" aria-label="Construction workers in hard hats and safety vests reviewing plans on site"></div>
<h1 class="hero__title">Building with Precision.<br>Serving with Kestrada.</h1>
<p class="hero__sub">General Contracting • Design-Build • Disaster Recovery<br>Environmental Remediation.</p>
<div class="btn btn--light" style="left:162px;top:502px;width:151px;height:36px">Work with us</div>

<svg class="abs" style="left:0;top:560px" width="1200" height="200">
  <polygon points="0,167 1200,60 1200,200 0,200" fill="var(--dark)"/>
  <polygon points="122,162 1200,58 1200,110 122,190" fill="var(--gold)"/>
</svg>

<!-- about -->
<section class="about"></section>
<h2 class="section-title" style="top:786px;color:var(--white)"><b>About</b> Us</h2>
<div class="about__text">
  <p>Lorem Ipsum is simply dummy text of the printing and typesetting industry. Lorem Ipsum has been the industry's standard dummy text ever since the 1500s, when an unknown printer took a galley of type and scrambled it to make a type specimen book.</p>
  <p>Lorem Ipsum is simply dummy text of the printing and typesetting industry. Lorem Ipsum has been the industry's standard dummy text ever since the 1500s.</p>
  <p>If you're able to become pregnant, you should use effective and reliable birth control while taking a GLP-1 agonist. If you become pregnant while taking the medication, see your healthcare provider immediately.</p>
</div>
<div class="btn" style="left:531px;top:1087px;width:137px;height:36px">Learn more</div>

<svg class="abs" style="left:0;top:1120px" width="1200" height="330">
  <polygon points="0,180 1200,10 1200,330 0,330" fill="var(--white)"/>
  <polygon points="0,150 946,48 946,78 0,190" fill="var(--beige)"/>
  <polygon points="0,160 600,170 0,318" fill="var(--beige)"/>
  <polygon points="0,150 946,48 946,58 0,200" fill="var(--gold)"/>
  <polygon points="0,200 560,170 0,250" fill="var(--gold)"/>
</svg>

<!-- services -->
<h2 class="section-title" style="top:1290px"><b>Our</b> Services</h2>

<div class="photo" style="left:600px;top:1399px;width:438px;height:391px;background:linear-gradient(135deg,#b9c4cf,#e3b15e 60%,#8a7b6b)" role="img" aria-label="Two construction workers in hard hats shaking hands on site"></div>
<div class="card" style="left:162px;top:1442px;width:483px;height:305px">
  <h3>General Contracting</h3>
  <p>Mobility, productivity, security, costs – which points are particularly important to you and your customers? Avoid friction losses right from the start and talk to an IT partner who understands your business and your concerns. Check us out, we are not afraid of comparison.</p>
  <p>Arrange a free initial consultation today.</p>
  <a>Learn More</a>
</div>

<div class="photo" style="left:162px;top:1866px;width:438px;height:391px;background:linear-gradient(135deg,#9ea3a6,#d8d2c6 40%,#e48b3a 75%,#8f8a84)" role="img" aria-label="Engineers in safety gear reviewing drawings beside a building under construction"></div>
<div class="card" style="left:553px;top:1909px;width:485px;height:305px">
  <h3>Design-Build Construction</h3>
  <p>Contact management, service recording, invoicing, automated correspondence, document management – this and more is what lawyers, trustees and asset managers need in their daily work.</p>
  <p>A specialized software solution can significantly increase your productivity, your billable hours and, above all, the satisfaction of your clients.</p>
  <a>Learn More</a>
</div>

<div class="photo" style="left:600px;top:2333px;width:438px;height:391px;background:linear-gradient(135deg,#c9ccd0,#7e7a73 45%,#e07a32 70%,#4f5a6a)" role="img" aria-label="Worker in hard hat and vest holding a clipboard at an industrial site"></div>
<div class="card" style="left:162px;top:2376px;width:483px;height:303px">
  <h3>Disaster Recovery</h3>
  <p>Increased mobility, better availability, lower CapEx, more flexibility – there are many reasons to outsource processes to the cloud.</p>
  <p>A cloud provider must devote enormous resources to security, which is why Norwell Systems maintains a partnership with the two largest and most financially strong providers in the world: Cloudwell and Skyforge.</p>
  <a>Learn More</a>
</div>

<div class="btn" style="left:520px;top:2771px;width:158px;height:35px">View all services</div>

<!-- projects -->
<svg class="abs" style="left:0;top:2810px" width="1200" height="100">
  <polygon points="0,78 1200,10 1200,100 0,100" fill="var(--dark)"/>
  <polygon points="0,78 800,78 1200,10 1200,30 820,92 0,92" fill="var(--dark)"/>
  <polygon points="800,90 1200,10 1200,40" fill="var(--gold)"/>
  <polygon points="780,80 1200,0 1200,12 800,90" fill="var(--beige)"/>
</svg>
<section class="projects"></section>
<h2 class="section-title" style="top:2996px;color:var(--white)"><b>Our</b> Projects</h2>

<div class="project" style="left:162px">
  <div class="photo" style="background:linear-gradient(160deg,#2c3f56,#6d7b86 50%,#4d5a3e)" role="img" aria-label="Technician and service member working at a server room"></div>
  <h4>Military / PMX Renovations</h4>
  <p>We have been active in IT for 20 years and are constantly continuing our training across a very broad spectrum.</p>
</div>
<div class="project" style="left:461px">
  <div class="photo" style="background:linear-gradient(180deg,#c9d3dc,#8c8a84 55%,#6b6d58)" role="img" aria-label="Hospital building under construction with cranes"></div>
  <h4>Hospital Renovations</h4>
  <p>We are interested in long-term relation-ships with our customers. We do not pursue short-term strategies.</p>
</div>
<div class="project" style="left:761px">
  <div class="photo" style="background:linear-gradient(180deg,#a9c3da,#c7c1b4 55%,#6e6a60)" role="img" aria-label="Large water pipeline laid along a construction trench"></div>
  <h4>Waterlines Construction</h4>
  <p>We understand that IT is a closed book for many of our customers. But that doesn't have to be the case.</p>
</div>
<div class="btn" style="left:520px;top:3537px;width:158px;height:35px">View all projects</div>

<!-- why -->
<h2 class="section-title" style="top:3735px"><b>Why Choose</b> Kestrada</h2>
<div class="why" style="left:244px">
  <div class="why__ring"><svg width="60" height="50" viewBox="0 0 60 50" fill="none" stroke="var(--gold)" stroke-width="2"><circle cx="30" cy="22" r="6"/><circle cx="15" cy="26" r="5"/><circle cx="45" cy="26" r="5"/><path d="M20 46c0-8 4-13 10-13s10 5 10 13zM6 46c0-6 4-10 9-10M54 46c0-6-4-10-9-10"/><path d="M30 3l2 4 4 .5-3 3 .8 4-3.8-2-3.8 2 .8-4-3-3 4-.5z"/></svg></div>
  <h5>Veteran-Owned Expertise<br>(SDVOSB)</h5>
</div>
<div class="why" style="left:496px">
  <div class="why__ring"><svg width="50" height="54" viewBox="0 0 50 54" fill="none" stroke="var(--gold)" stroke-width="2"><path d="M8 4h26l8 8v38H8z"/><path d="M15 16h18M15 23h20M15 30h12"/><circle cx="36" cy="40" r="8"/><path d="M32 40l3 3 5-6"/></svg></div>
  <h5>Government Contracting<br>Experience</h5>
</div>
<div class="why" style="left:748px">
  <div class="why__ring"><svg width="48" height="54" viewBox="0 0 48 54" fill="none" stroke="var(--gold)" stroke-width="2"><path d="M24 3l19 7v16c0 13-9 21-19 25C14 47 5 39 5 26V10z"/><path d="M15 27l7 7 12-13"/></svg></div>
  <h5>Precision, Safety, And<br>Compliance</h5>
</div>

<!-- clients -->
<h2 class="section-title" style="top:4018px"><b>Our</b> Clients</h2>
<div class="client" style="left:126px"><div class="client__mark" style="background:#2f4f86"></div><h6>PMX</h6></div>
<div class="client" style="left:308px"><div class="client__mark" style="background:#3a3f6e"></div><h6>TQ</h6></div>
<div class="client" style="left:495px"><div class="client__mark" style="background:#3d6b56"></div><h6>State and Local<br>Gov't Agencies</h6></div>
<div class="client" style="left:675px"><div class="client__mark" style="background:#d8b64e"></div><h6>Hospitals</h6></div>
<div class="client" style="left:859px"><div class="client__mark" style="background:#c43a3a"></div><h6>Schools</h6></div>

<!-- contact -->
<div class="photo contact-photo" role="img" aria-label="Architectural blueprints, calculator and yellow hard hat on a desk"></div>
<div class="contact-card">
  <div class="contact-card__eyebrow">Contact</div>
  <div class="contact-card__title">Get In Touch</div>
  <div class="field" style="left:44px;top:162px;width:180px">Name*</div>
  <div class="field" style="left:261px;top:162px;width:176px">Last Name</div>
  <div class="field" style="left:44px;top:224px;width:180px">Phone</div>
  <div class="field" style="left:261px;top:224px;width:176px">Email Address*</div>
  <div class="field" style="left:44px;top:286px;width:393px">Service</div>
  <div class="field" style="left:44px;top:348px;width:393px;height:68px">Your Message</div>
  <div class="btn" style="left:161px;top:514px;width:154px;height:36px">Submit</div>
</div>
<div class="captcha" style="left:486px"><i></i>I'm not a robot<b></b></div>

<!-- footer -->
<footer class="footer">
  <div class="logo" style="left:160px;top:104px;font-size:24px"><i style="width:16px;height:16px"></i>KESTRADA</div>
  <div class="footer__col" style="left:424px"><h6>Quick Links</h6><ul><li>Home</li><li>About Us</li><li>Services</li><li>Contact</li></ul></div>
  <div class="footer__col" style="left:602px"><h6>Services</h6><ul><li>General Contracting</li><li>Design-Build Construction</li><li>Disaster Recovery</li><li>Environmental Remediation</li></ul></div>
  <div class="footer__col" style="left:819px;width:220px"><h6>Contact Us</h6>
    <div class="footer__row" style="margin:16px 0 12px 6px"><svg width="12" height="12" viewBox="0 0 24 24"><path fill="#fff" d="M6.6 10.8a15 15 0 0 0 6.6 6.6l2.2-2.2a1 1 0 0 1 1-.25 11.4 11.4 0 0 0 3.6.57 1 1 0 0 1 1 1V20a1 1 0 0 1-1 1A17 17 0 0 1 3 4a1 1 0 0 1 1-1h3.5a1 1 0 0 1 1 1c0 1.25.2 2.45.57 3.57a1 1 0 0 1-.25 1z"/></svg>+1 555 014 2270</div>
    <div class="footer__row" style="margin-left:6px;padding-bottom:14px;border-bottom:1px solid #777"><svg width="13" height="10" viewBox="0 0 26 20"><rect width="26" height="20" fill="#fff"/><path d="M0 0l13 10L26 0" stroke="var(--dark)" stroke-width="2" fill="none"/></svg>hello@kestrada-build.com</div>
    <div class="footer__social"><span></span><span></span><span></span></div>
  </div>
  <div class="footer__copy">© 2025 kestrada. All Rights Reserved</div>
</footer>

</body>
</html>
```